Lantern Petals Website v.1 - attract floral shop franchisees

I need a simple information website for my new business. We are a franchisor of flower shops. The overall purpose of the website is to promote the company and the service, especially to potential franchisees and retailers. Only about 4 pages are required including homepage, About, For Supermarkets, For Franchisees, and Contact. No special functions are required except the site will have two separate inquiry forms that must be filled out online and submitted via automated email. Similarly, an email form should be linked from the Contact page. I have a logo and business cards designed by ArtMingle, and I would like the site to have a consistent color scheme and style. The key to design will be to express the joy and love associated with flowers and floral bouquets.
IMPORTANT - I will be exporting the website design to Wordpress CMS in a site hosted by HostNimbus. For smooth integration into WordPress hosted by HostNimbus, the designer should build the site using a WordPress-friendly format. Ideally, they should use HTML, CSS, and PHP. Creating a custom theme or using a page builder that exports to WordPress-compatible files is best. This ensures the site can be easily imported and managed within WordPress.

Target Market(s)

Potential franchisees (existing florists or creative types who might like to own a floral business) and supermarkets who might want us to run their floral department

Industry/Entity Type

Floral retailing

Requirements
Must have
• A brand theme that is beautiful, consistent throughout and builds on the logo design
Nice to have
• Show gender and ethnic diversity in customers and florists. Pictures of happy florists (for franchisees) and pictures of amazing floral department displays (for supermarkets)

```html
<!DOCTYPE html>
<html lang="en">
<head>
<meta charset="utf-8">
<title>Lantern Petals</title>
<link href="https://fonts.googleapis.com/css2?family=Great+Vibes&family=Montserrat:wght@500;600;700;800&family=Poppins:wght@400;500;600&display=swap" rel="stylesheet">
<style>
:root{
  --green:#1b8f48;
  --green-dark:#137a3b;
  --orange:#f29b21;
  --orange-deep:#e88a12;
  --cream:#fdf2df;
  --ink:#4e4e4e;
  --night:#10261a;
  --white:#ffffff;
}
*{margin:0;padding:0;box-sizing:border-box}
html,body{width:1200px;height:5042px;overflow:hidden;background:var(--white)}
body{position:relative;font-family:"Poppins",sans-serif;color:var(--ink)}
.abs{position:absolute}
.script{font-family:"Great Vibes",cursive;color:var(--orange);font-size:34px;line-height:1}
.heading{font-family:"Montserrat",sans-serif;font-weight:700;color:var(--green);font-size:36px;letter-spacing:1.5px;line-height:44px;text-transform:uppercase}
.body-text{font-size:14.5px;line-height:31px;color:var(--ink)}
.pill{position:absolute;display:flex;align-items:center;justify-content:space-between;height:46px;border-radius:23px;background:var(--orange);color:var(--white);font-family:"Montserrat",sans-serif;font-weight:700;font-size:11.5px;letter-spacing:.5px;padding:0 5px 0 20px;text-transform:uppercase;line-height:14px}
.pill.green{background:var(--green)}
.pill .dot{width:38px;height:38px;border-radius:50%;background:var(--white);border:2px solid var(--orange);display:flex;align-items:center;justify-content:center}
.pill.green .dot{border-color:var(--green)}
.photo{position:absolute}
/* header */
.site-header{position:absolute;top:0;left:0;width:1200px;height:104px;background:var(--white);z-index:5}
.brand{position:absolute;display:flex;align-items:center;gap:10px;font-family:"Montserrat",sans-serif;font-weight:700;font-size:24px;color:var(--orange)}
.brand .mark{width:26px;height:26px;border-radius:50%;background:var(--green)}
.nav a{position:absolute;top:45px;font-family:"Montserrat",sans-serif;font-size:12px;font-weight:600;color:#666;text-decoration:none;letter-spacing:.3px}
.nav a.current{color:var(--green);font-weight:700}
/* hero */
.hero-title{font-family:"Montserrat",sans-serif;font-weight:800;color:var(--green);font-size:46px;letter-spacing:4px;line-height:56px}
.opp-text{position:absolute;font-size:14.5px;line-height:31px;color:var(--ink);width:280px}
.opp-text.right{text-align:right}
.footer-title{font-family:"Montserrat",sans-serif;font-weight:600;color:var(--white);font-size:16px;letter-spacing:1px}
.footer-links a{display:block;color:var(--white);font-size:14px;line-height:30px;text-decoration:none}
.footer-text{color:var(--white);font-size:14px;line-height:30px}
.icon-ring{position:absolute;width:44px;height:44px;border-radius:50%;background:var(--green);display:flex;align-items:center;justify-content:center}
</style>
</head>
<body>

<!-- HEADER -->
<header class="site-header">
  <div class="brand" style="left:120px;top:34px"><span class="mark"></span>Lantern Petals</div>
  <nav class="nav">
    <a class="current" href="#" style="left:485px">HOME</a>
    <a href="#" style="left:560px">ABOUT US</a>
    <a href="#" style="left:647px">SUPERMARKETS</a>
    <a href="#" style="left:790px">FRANCHISEES</a>
  </nav>
  <svg class="abs" style="left:490px;top:25px" width="20" height="14" viewBox="0 0 20 14"><path d="M2 12 C4 2 14 0 18 2 C16 10 8 13 2 12Z" fill="var(--green)"/></svg>
  <div class="pill" style="left:934px;top:31px;width:145px;height:42px;font-size:11px"><span>CONTACT</span><span class="dot" style="width:34px;height:34px"><svg width="14" height="16" viewBox="0 0 14 16"><path d="M7 15V5M7 9C4 8 3 6 3 3M7 7C10 6 11 4 11 1" stroke="var(--green)" stroke-width="1.6" fill="none"/></svg></span></div>
</header>

<!-- HERO -->
<section class="abs" style="left:0;top:104px;width:1200px;height:700px">
  <div class="photo" role="img" aria-label="Photo of a bright bouquet with roses, a sunflower and wildflowers against a soft grey backdrop" style="left:0;top:0;width:1200px;height:700px;background:linear-gradient(100deg,#ebe8ea 0%,#e9e3e3 40%,#eab9a0 58%,#f2c64a 72%,#6d8a45 84%,#c9b7d9 100%)"></div>
  <div class="script abs" style="left:120px;top:134px;font-size:44px">Fresh Flowers</div>
  <h1 class="hero-title abs" style="left:120px;top:192px">CONVEY BEAUTY<br>AND LOVE</h1>
  <div class="pill" style="left:120px;top:323px;width:170px;height:48px"><span>GET STARTED</span><span class="dot"><svg width="14" height="16" viewBox="0 0 14 16"><path d="M7 15V5M7 9C4 8 3 6 3 3M7 7C10 6 11 4 11 1" stroke="var(--green)" stroke-width="1.6" fill="none"/></svg></span></div>
  <svg class="abs" style="left:0;top:450px" width="1200" height="252" viewBox="0 0 1200 252" preserveAspectRatio="none">
    <path d="M0 130 C220 110 380 190 520 250 L0 252Z" fill="var(--green)"/>
    <path d="M0 140 C150 130 300 190 470 230 C600 250 760 252 860 240 C1000 220 1120 150 1200 70 L1200 252 L0 252Z" fill="var(--white)"/>
    <path d="M0 30 C260 40 430 220 760 240 C950 250 1110 150 1200 80 L1200 110 C1120 170 960 262 780 252 C480 240 300 110 0 100Z" fill="var(--orange)"/>
    <path d="M0 100 C300 110 480 240 780 252 L0 252Z" fill="var(--white)"/>
    <path d="M0 125 C160 118 300 170 420 215 C300 190 150 165 0 180Z" fill="var(--green)"/>
  </svg>
</section>

<!-- ABOUT -->
<section class="abs" style="left:0;top:820px;width:1200px;height:600px">
  <div class="photo" role="img" aria-label="Illustration of a honeycomb flower with a stem, a small bee and a ring" style="left:118px;top:40px;width:390px;height:510px;border-radius:48% 48% 50% 50%;background:radial-gradient(circle at 55% 30%,#f6c25a 0%,#f0a73a 30%,#5ea85f 62%,#ffffff 78%)"></div>
  <div class="script abs" style="left:609px;top:75px">About Us</div>
  <h2 class="heading abs" style="left:609px;top:116px">Lantern Petals</h2>
  <p class="body-text abs" style="left:609px;top:170px;width:480px">Lantern Petals is an entrepreneurial company created to make top quality fresh flowers and professionally-designed bouquets accessible to every consumer at affordable prices.</p>
  <p class="body-text abs" style="left:609px;top:290px;width:480px">Professional florists typically sell the finest quality stems, design the most beautiful bouquets and provide the finest customer service, but their costs – of floral products, retail spaces, labor and marketing – force them to pass high prices along to customers.</p>
  <div class="pill" style="left:609px;top:469px;width:162px"><span>READ MORE</span><span class="dot"><svg width="14" height="16" viewBox="0 0 14 16"><path d="M7 15V5M7 9C4 8 3 6 3 3M7 7C10 6 11 4 11 1" stroke="var(--green)" stroke-width="1.6" fill="none"/></svg></span></div>
</section>

<!-- SUPERMARKETS -->
<section class="abs" style="left:0;top:1459px;width:1200px;height:744px">
  <svg class="abs" style="left:0;top:0" width="1200" height="744" viewBox="0 0 1200 744" preserveAspectRatio="none" role="img" aria-label="Green band with a faint photo of flowers">
    <defs><linearGradient id="greenBg" x1="0" y1="0" x2="1" y2="1"><stop offset="0" stop-color="#1e9350"/><stop offset="1" stop-color="#17883f"/></linearGradient></defs>
    <path d="M0 230 C260 110 420 20 620 30 C800 40 980 110 1200 60 L1200 744 L0 744Z" fill="url(#greenBg)"/>
    <path d="M390 15 C620 -10 800 80 1000 110 C1090 122 1160 100 1200 80 L1200 225 C1120 210 1020 170 900 120 C740 55 600 20 390 15Z" fill="var(--orange)"/>
    <path d="M820 70 C960 95 1080 90 1200 20 L1200 55 C1080 115 960 110 820 70Z" fill="var(--green)"/>
  </svg>
  <div class="script abs" style="left:120px;top:262px;font-size:30px">Best in Supermarkets</div>
  <h2 class="heading abs" style="left:118px;top:305px;color:var(--white);line-height:44px">Professional Florists<br>in the Supermarkets</h2>
  <p class="body-text abs" style="left:120px;top:402px;width:470px;color:var(--white)">Lantern Petals brings the best of professional florists and supermarkets together for the benefit of consumers.</p>
  <p class="body-text abs" style="left:120px;top:493px;width:480px;color:var(--white)">It supports a national network of owner-operator franchisees, who in many cases are multi-site professional florists, with comprehensive services to enhance franchise profitability.</p>
  <div class="pill" style="left:120px;top:611px;width:162px"><span>READ MORE</span><span class="dot"><svg width="14" height="16" viewBox="0 0 14 16"><path d="M7 15V5M7 9C4 8 3 6 3 3M7 7C10 6 11 4 11 1" stroke="var(--green)" stroke-width="1.6" fill="none"/></svg></span></div>
  <svg class="abs" style="left:670px;top:250px" width="420" height="420" viewBox="0 0 420 420">
    <path d="M247 12 A198 198 0 1 1 120 28" fill="none" stroke="var(--white)" stroke-width="7"/>
  </svg>
  <div class="photo" role="img" aria-label="Photo of hands holding a pink pot of red and pink roses" style="left:694px;top:274px;width:366px;height:366px;border-radius:50%;background:radial-gradient(circle at 45% 45%,#e0486b 0%,#f08aa0 35%,#f3c9c4 70%,#e9d8d2 100%)"></div>
  <div class="abs" style="left:980px;top:535px;width:96px;height:96px;border-radius:50%;background:var(--white);box-shadow:0 0 0 6px rgba(255,255,255,.5)"></div>
</section>

<!-- OPPORTUNITY -->
<section class="abs" style="left:0;top:2203px;width:1200px;height:760px">
  <div class="photo" role="img" aria-label="Small illustration of a bee with a dotted flight trail" style="left:118px;top:70px;width:96px;height:120px;border-radius:40%;background:linear-gradient(160deg,rgba(242,155,33,.35),rgba(27,143,72,.25))"></div>
  <div class="script abs" style="left:0;top:88px;width:1200px;text-align:center;font-size:30px">Best in Opportunity</div>
  <h2 class="heading abs" style="left:0;top:126px;width:1200px;text-align:center">Supermarkets Opportunity</h2>
  <p class="opp-text right" style="left:211px;top:204px">Enhance floral revenue streams with efficient assortments and new offerings</p>
  <p class="opp-text" style="left:709px;top:204px">Provide attentive customer service, including semi-custom bouquets, by professional florist staff</p>
  <p class="opp-text right" style="left:129px;top:382px">Reduce the costs of operating a floral department</p>
  <p class="opp-text" style="left:791px;top:382px">Maintain a beautiful, fresh and well-stocked environment</p>
  <p class="opp-text right" style="left:211px;top:570px">Improve the quality, useful life and merchandising of floral products</p>
  <p class="opp-text" style="left:709px;top:570px">Enhance the entire customer shopping environment</p>
  <svg class="abs" style="left:0;top:0" width="1200" height="760" viewBox="0 2203 1200 760">
    <g stroke="var(--white)" stroke-width="3" stroke-linejoin="round">
      <polygon points="601,2649 601,2471 447,2560" fill="var(--green)"/>
      <polygon points="601,2649 601,2471 755,2560" fill="var(--orange)"/>
      <polygon points="601,2649 755,2560 755,2738" fill="var(--green)"/>
      <polygon points="601,2649 755,2738 601,2827" fill="var(--orange)"/>
      <polygon points="601,2649 601,2827 447,2738" fill="var(--green)"/>
      <polygon points="601,2649 447,2738 447,2560" fill="var(--orange)"/>
    </g>
    <g fill="none" stroke="var(--white)" stroke-width="2.5" stroke-linecap="round" stroke-linejoin="round">
      <!-- percent badge -->
      <circle cx="550" cy="2560" r="22"/>
      <line x1="541" y1="2570" x2="559" y2="2550"/>
      <circle cx="542" cy="2552" r="3"/><circle cx="558" cy="2568" r="3"/>
      <!-- florist -->
      <circle cx="652" cy="2550" r="9"/>
      <path d="M634 2582 C636 2568 668 2568 670 2582Z"/>
      <path d="M642 2546 C646 2536 658 2536 662 2546"/>
      <!-- plant -->
      <path d="M703 2672 V2640 M703 2655 C690 2652 684 2642 686 2630 C698 2632 703 2642 703 2655 M703 2650 C716 2647 722 2637 720 2625 C708 2627 703 2637 703 2650"/>
      <!-- basket -->
      <path d="M632 2730 H672 L666 2758 H638Z M640 2730 L648 2716 M664 2730 L656 2716 M645 2738 V2750 M652 2738 V2750 M659 2738 V2750"/>
      <!-- tulip -->
      <path d="M550 2762 V2738 M538 2720 C538 2734 562 2734 562 2720 L556 2726 L550 2716 L544 2726Z M550 2752 C540 2748 536 2742 536 2736 M550 2752 C560 2748 564 2742 564 2736"/>
      <!-- tag -->
      <path d="M482 2658 L508 2632 L522 2632 L522 2646 L496 2672Z"/>
      <circle cx="515" cy="2639" r="2.5"/>
      <line x1="494" y1="2654" x2="506" y2="2642"/>
    </g>
  </svg>
</section>

<!-- FRANCHISEES -->
<section class="abs" style="left:0;top:2957px;width:1200px;height:724px">
  <svg class="abs" style="left:0;top:0" width="1200" height="724" viewBox="0 0 1200 724" preserveAspectRatio="none">
    <path d="M0 215 C400 130 800 80 1200 80 L1200 724 L0 724Z" fill="var(--cream)"/>
    <path d="M0 130 C280 75 560 20 820 0 C980 -8 1120 20 1200 30 L1200 82 C800 80 400 130 0 215Z" fill="var(--orange)"/>
    <path d="M0 55 C180 25 420 5 800 0 C520 30 260 70 0 132Z" fill="var(--green)"/>
  </svg>
  <svg class="abs" style="left:120px;top:230px" width="430" height="430" viewBox="0 0 430 430">
    <path d="M335 50 A200 200 0 1 0 405 150" fill="none" stroke="var(--orange)" stroke-width="8"/>
    <path d="M355 130 A170 170 0 0 1 340 330" fill="none" stroke="var(--white)" stroke-width="3"/>
  </svg>
  <div class="photo" role="img" aria-label="Photo of a smiling florist holding a vase of white roses in his shop" style="left:146px;top:256px;width:378px;height:378px;border-radius:50%;background:linear-gradient(160deg,#cfd6cf 0%,#7d8f86 45%,#2d3b55 75%,#bfc7c0 100%)"></div>
  <div class="script abs" style="left:630px;top:235px;font-size:30px">About Us</div>
  <h2 class="heading abs" style="left:630px;top:276px">Lantern Petals<br>Franchisees</h2>
  <p class="body-text abs" style="left:630px;top:374px;width:460px">Lantern Petals works with some of the country’s largest and most progressive supermarkets to provide franchisee ownership and operation of their strategically important floral departments.</p>
  <div class="abs" style="left:630px;top:513px;font-family:'Montserrat',sans-serif;font-weight:700;font-size:13px;letter-spacing:.8px;color:#3a3a3a">OUR FRANCHISEES INQUIRY:</div>
  <div class="pill" style="left:630px;top:552px;width:214px;font-size:10.5px"><span>FOR NEW<br>FLORIST FRANCHISE</span><span class="dot"><svg width="14" height="16" viewBox="0 0 14 16"><path d="M7 15V5M7 9C4 8 3 6 3 3M7 7C10 6 11 4 11 1" stroke="var(--green)" stroke-width="1.6" fill="none"/></svg></span></div>
  <div class="pill green" style="left:860px;top:552px;width:212px;font-size:10.5px"><span>PROFESSIONAL<br>FLORIST FRANCHISE</span><span class="dot"><svg width="14" height="16" viewBox="0 0 14 16"><path d="M7 15V5M7 9C4 8 3 6 3 3M7 7C10 6 11 4 11 1" stroke="var(--green)" stroke-width="1.6" fill="none"/></svg></span></div>
</section>

<!-- GALLERY -->
<section class="abs" style="left:0;top:3681px;width:1200px;height:680px">
  <div class="script abs" style="left:0;top:76px;width:1200px;text-align:center;font-size:30px">Images</div>
  <h2 class="heading abs" style="left:0;top:114px;width:1200px;text-align:center">Our Gallery</h2>
  <div class="photo" role="img" aria-label="Photo of a bouquet of red roses tied with a red ribbon on a grey table" style="left:120px;top:204px;width:330px;height:432px;background:linear-gradient(150deg,#4a5560 0%,#a3141f 40%,#c8232d 60%,#3f4a52 100%)"></div>
  <div class="photo" role="img" aria-label="Photo of peonies in small glass vases" style="left:462px;top:204px;width:331px;height:213px;background:linear-gradient(120deg,#5a6570 0%,#a8336b 35%,#f0ede8 60%,#66727c 100%)"></div>
  <div class="photo" role="img" aria-label="Photo of pink tulips on a pink background" style="left:462px;top:427px;width:331px;height:209px;background:linear-gradient(135deg,#f6b8c4 0%,#d98fc8 45%,#f3a6b6 75%,#f8c6cf 100%)"></div>
  <div class="photo" role="img" aria-label="Photo of a pink and magenta rose bouquet with white baby's breath" style="left:803px;top:204px;width:276px;height:432px;background:linear-gradient(160deg,#2e4a34 0%,#c2395f 40%,#e26a8a 60%,#2d4433 100%)"></div>
</section>

<!-- FOOTER -->
<footer class="abs" style="left:0;top:4410px;width:1200px;height:632px">
  <div class="photo" role="img" aria-label="Small illustration of a bee with a dotted flight trail" style="left:118px;top:3px;width:96px;height:120px;border-radius:40%;background:linear-gradient(160deg,rgba(242,155,33,.35),rgba(27,143,72,.25))"></div>
  <svg class="abs" style="left:0;top:44px" width="1200" height="588" viewBox="0 0 1200 588" preserveAspectRatio="none">
    <path d="M0 230 C260 150 460 70 700 100 C900 125 1050 190 1200 150 L1200 588 L0 588Z" fill="var(--night)"/>
    <path d="M390 45 C640 10 880 90 1040 120 C1110 132 1170 120 1200 105 L1200 175 C1120 195 1000 160 860 120 C700 80 560 55 390 45Z" fill="var(--orange)"/>
    <path d="M720 65 C880 70 1040 130 1200 60 L1200 100 C1050 160 880 100 720 65Z" fill="var(--green)"/>
  </svg>
  <div class="brand" style="left:120px;top:345px;font-size:26px"><span class="mark" style="background:var(--orange)"></span>Lantern Petals</div>
  <p class="footer-text abs" style="left:120px;top:405px;width:300px">Lantern Petals is an entrepreneurial company created to make top quality fresh flowers and professionally</p>
  <div class="abs" style="left:480px;top:280px;width:1px;height:200px;background:rgba(255,255,255,.2)"></div>
  <div class="abs" style="left:746px;top:280px;width:1px;height:200px;background:rgba(255,255,255,.2)"></div>
  <div class="footer-title abs" style="left:556px;top:296px">QUICK LINKS</div>
  <nav class="footer-links abs" style="left:556px;top:333px">
    <a href="#">Home</a><a href="#">About Us</a><a href="#">Supermarkets</a><a href="#">Franchisees</a><a href="#">Contact</a>
  </nav>
  <div class="footer-title abs" style="left:822px;top:296px">CONTACT INFO</div>
  <div class="icon-ring" style="left:822px;top:343px"><svg width="18" height="18" viewBox="0 0 24 24"><path d="M6 3 L9 3 L11 8 L8.5 9.5 C9.5 12 12 14.5 14.5 15.5 L16 13 L21 15 L21 18 C21 20 19 21 17 21 C10 20 4 14 3 7 C3 5 4 3 6 3Z" fill="none" stroke="var(--white)" stroke-width="1.8" stroke-linejoin="round"/></svg></div>
  <div class="icon-ring" style="left:822px;top:402px"><svg width="18" height="18" viewBox="0 0 24 24"><rect x="3" y="5" width="18" height="14" rx="2" fill="none" stroke="var(--white)" stroke-width="1.8"/><path d="M3 7 L12 13 L21 7" fill="none" stroke="var(--white)" stroke-width="1.8"/></svg></div>
  <p class="footer-text abs" style="left:883px;top:335px">Phone:<br>+1 555 310 0147</p>
  <p class="footer-text abs" style="left:883px;top:395px;width:200px">For questions and further information, contact<br><span style="color:var(--orange);text-decoration:underline">info@lanternpetals.com</span></p>
  <p class="abs" style="left:0;top:578px;width:1200px;text-align:center;color:var(--white);font-size:13.5px">Copyright © 2024 Lantern Petals All rights reserved.</p>
</footer>

</body>
</html>
```